Wordpress Design Project SEO/SEM Website

Need an updated more professional look for an SEO/SEM existing site.
see: www.brightquill-hub.com

I have an existing logo (in eps format), but am flexible on color and would consider updating the logo if the current colors or design limits your creativity.

Target Market(s)

My customers tend to be marketing managers for mid-size companies with 50+ employees.

Industry/Entity Type

Marketing

Requirements
Must have
• Design should support WordPress 3.0 menus, and widgets.
Nice to have
• Should you want/need it, the font used in the logo is 'ARTLOOKIN'
Should not have
• flash

```html
<!DOCTYPE html>
<html lang="en">
<head>
<meta charset="utf-8">
<title>Brightquill Hub – SEO / SEM Services</title>
<link href="https://fonts.googleapis.com/css2?family=Crimson+Text:wght@400;600&family=Source+Sans+3:ital,wght@0,400;0,600;0,700;1,400&display=swap" rel="stylesheet">
<style>
:root{
  --topbar:#0f5d85;
  --topbar-dark:#0b4a6b;
  --header:#2b2b2b;
  --header-dark:#1c1c1c;
  --nav-top:#2a8bc8;
  --nav-bottom:#1166a2;
  --nav-active:#47a6dc;
  --sky-top:#bfe6f8;
  --sky-bottom:#e6f6fd;
  --hero-warm-light:#f7d9b8;
  --hero-warm:#ee9a52;
  --brand-blue:#1a6fa8;
  --link-blue:#1b78b5;
  --heading:#2d2d2d;
  --body:#4a4a4a;
  --rule:#d6d6d6;
  --footer:#0f5d85;
  --page:#eef1f3;
  --white:#ffffff;
}
*{margin:0;padding:0;box-sizing:border-box}
html,body{width:878px;height:1200px;overflow:hidden}
body{position:relative;background:var(--page);font-family:"Source Sans 3",Arial,sans-serif;color:var(--body);font-size:10px;line-height:12.5px}
a{color:inherit;text-decoration:none}
.abs{position:absolute}

/* top bar */
.topbar{left:0;top:0;width:878px;height:22px;background:var(--topbar)}
.member-links{left:650px;top:0;width:200px;height:22px;background:var(--topbar-dark);color:#dbeaf3;font-size:10px;line-height:22px;text-align:center}

/* header */
.masthead{left:0;top:22px;width:878px;height:118px;background:linear-gradient(var(--header),var(--header-dark))}
.brand{left:34px;top:58px;display:flex;align-items:flex-end;gap:12px;color:var(--white);font-size:23px;line-height:28px}
.brand-dot{width:62px;height:62px;border-radius:50%;background:#3b8fc4}
.search{left:650px;top:103px;width:200px;height:22px;border-radius:11px;background:#3a3a3a;border:1px solid #555;color:#9a9a9a;font-size:10px;line-height:20px;padding-left:10px}
.search svg{position:absolute;right:8px;top:4px}

/* navigation */
.main-nav{left:0;top:140px;width:878px;height:47px;background:linear-gradient(var(--nav-top),var(--nav-bottom));display:flex;padding-left:30px}
.main-nav a{color:#e8f3fa;font-size:13.5px;line-height:47px;text-align:center;border-right:1px solid #3f97cf}
.main-nav a.active{background:var(--nav-active);color:var(--white)}

/* hero */
.hero{left:0;top:187px;width:878px;height:280px;background:linear-gradient(var(--sky-top),var(--sky-bottom))}
.hero-title{left:54px;top:243px;font-family:"Crimson Text",Georgia,serif;font-size:28px;line-height:34px;color:var(--brand-blue);font-weight:600}
.hero-title span{font-weight:400}
.hero-copy{left:55px;top:282px;width:410px;color:#1f6b9c;font-size:10.5px;line-height:13.5px}
.hero-copy p{margin-bottom:5px}
.hero-button{left:52px;top:389px;width:162px;height:24px;border-radius:12px;background:linear-gradient(#3f8fc7,#1d66a0);border:1px solid #7ab7df;color:var(--white);font-size:11px;line-height:22px;text-align:center}
.hero-art{left:495px;top:230px;width:315px;height:237px;background:linear-gradient(135deg,var(--hero-warm-light),var(--hero-warm))}

/* content panel */
.panel{left:15px;top:467px;width:848px;height:650px;background:var(--white)}
.footer{left:0;top:1097px;width:878px;height:103px;background:var(--footer)}
.column-rule{left:595px;top:482px;width:1px;height:590px;background:var(--rule)}

h2.section-title{font-weight:400;font-size:18px;line-height:22px;color:var(--heading)}
h2.section-title em{font-style:normal;color:var(--link-blue)}
.copy p{margin-bottom:7px}
.read-more{display:block;width:154px;height:18px;border:1px solid #ccc;border-radius:0 9px 9px 0;font-size:10px;line-height:16px;padding-left:7px;color:#333;background:linear-gradient(#fff,#f0f0f0)}

.welcome{left:32px;top:486px;width:545px}
.welcome .copy{margin-top:9px;padding-left:3px}

.feature{top:676px;width:165px}
.feature-head{display:flex;align-items:center;gap:8px;font-size:14px;color:#222;height:40px}
.feature-icon{width:30px;height:30px;border-radius:4px;flex:none}
.feature-lead{color:var(--link-blue);font-weight:700;font-size:9.5px;line-height:12px;margin:6px 0 10px}
.feature-rule{top:670px;width:1px;height:160px;background:linear-gradient(#fff,#ddd,#fff)}

.about{left:32px;top:865px;width:545px}
.about .copy{margin-top:8px}

/* sidebar */
.side-title{font-weight:400;font-size:16px;line-height:20px;color:#1e1e1e}
.post-title{color:var(--link-blue);font-size:11.5px;line-height:15px;width:200px}
.post-text{width:228px}
.post-date{font-size:9px;color:#222}
.view-all{left:619px;top:742px;width:220px;height:14px;background:var(--link-blue);color:var(--white);font-size:9px;line-height:14px;text-align:right;padding-right:8px}
.dotted{left:619px;top:775px;width:222px;border-top:2px dotted #bbb}
.testimonial{left:612px;top:822px;width:239px;height:124px;border:1px solid #ccd;border-radius:10px;background:#f4f6f8;padding:12px 10px 0 11px;font-style:italic;font-size:10px;line-height:13.6px}
.testimonial cite{display:block;text-align:right;color:var(--link-blue);font-size:11.5px;margin-top:5px}
.connect{left:612px;top:979px;width:228px;height:23px;border-radius:0 12px 12px 0;background:#eee;padding-left:13px;font-size:15px;line-height:23px;color:#222}
.social-icons{left:625px;top:1012px;display:flex;gap:5px}
.social-icons span{width:20px;height:20px;border-radius:3px}
.social-links{left:626px;top:1041px;font-size:10px;color:#222}

.footer-left{left:18px;top:1127px;color:#e4eef5;font-size:10px;line-height:17px}
.footer-nav{right:21px;top:1127px;color:#e4eef5;font-size:10px;line-height:17px}
</style>
</head>
<body>
<div class="abs topbar"></div>
<div class="abs member-links"><a href="#">Member Log In</a> | <a href="#">Sign Up</a> | <a href="#">Register</a></div>

<header class="abs masthead"></header>
<div class="abs brand"><span class="brand-dot"></span>Brightquill Hub</div>
<div class="abs search">type your word here..
  <svg width="14" height="14" viewBox="0 0 14 14"><circle cx="5.5" cy="5.5" r="4" fill="none" stroke="#999" stroke-width="1.5"/><line x1="8.5" y1="8.5" x2="13" y2="13" stroke="#999" stroke-width="2"/></svg>
</div>

<nav class="abs main-nav">
  <a class="active" href="#" style="width:92px">Home</a>
  <a href="#" style="width:113px">About Us</a>
  <a href="#" style="width:116px">Services</a>
  <a href="#" style="width:84px">SEO</a>
  <a href="#" style="width:86px">SEM</a>
  <a href="#" style="width:132px">Recent Blog</a>
  <a href="#" style="width:136px;border-right:0">Contact Us</a>
</nav>

<section class="abs hero"></section>
<h1 class="abs hero-title">SEO Services <span>Goes here..</span></h1>
<div class="abs hero-copy">
  <p>Northvale eSolutions is specialized in handling advanced web projects and the ongoing projects that require permanent maintenance and support .</p>
  <p>We like challenges and do complete these challenge with expertise we like solving questions that arises in such projects as these helps us to grow also. When considering advanced web development project, finding the right answers to the hard questions is a challenge for any firm, it includes expertise and enables</p>
</div>
<a class="abs hero-button" href="#">VIEW OUR MORE SERVICES</a>
<div class="abs hero-art" role="img" aria-label="Illustration of a globe ringed by a chain of orange figures holding hands"></div>

<div class="abs footer"></div>
<main class="abs panel"></main>
<div class="abs column-rule"></div>

<section class="abs welcome">
  <h2 class="section-title">Welcome to <em>Brightquill Hub Mainpage..</em></h2>
  <div class="copy">
    <p>E-Commerce is a major progress in technology that has changed the way in which the customers now purchase information, products and the services. It's the new way of providing an opportunity to make your products and services available in the global market 24 hours a day through Internet</p>
    <p>Northvale eSolutions is specialized in handling advanced web projects and the ongoing projects that require permanent maintenance and support .We like challenges and do complete these challenge with expertise we like solving questions that arises in such projects as these helps us to grow also. When considering advanced web development project, finding the right answers to the hard questions is a challenge for any firm, it includes expertise and enables</p>
  </div>
</section>
<a class="abs read-more" href="#" style="left:30px;top:621px">CLICK HERE TO READ MORE</a>

<article class="abs feature" style="left:38px">
  <div class="feature-head"><span class="feature-icon" style="background:#5a6b80"></span>Internet Marketing</div>
  <p class="feature-lead">Static website are the which are usually been used and are benefited through the Professionals and Small Companies.</p>
  <p>The companies with fewer budgets can promote their products and services through the static website and gain a lot.</p>
</article>
<div class="abs feature-rule" style="left:211px"></div>
<article class="abs feature" style="left:227px">
  <div class="feature-head"><span class="feature-icon" style="background:#3a8fcf;border-radius:50%"></span>SEO Services</div>
  <p class="feature-lead">Static website are the which are usually been used and are benefited through the Professionals and Small Companies.</p>
  <p>The companies with fewer budgets can promote their products and services through the static website and gain a lot.</p>
</article>
<div class="abs feature-rule" style="left:400px"></div>
<article class="abs feature" style="left:417px">
  <div class="feature-head">
    <svg class="feature-icon" viewBox="0 0 30 30" aria-hidden="true"><rect x="2" y="18" width="7" height="10" fill="#e24a2a"/><rect x="11" y="11" width="7" height="17" fill="#f0b020"/><rect x="20" y="3" width="7" height="25" fill="#6bb52a"/></svg>SEM Services</div>
  <p class="feature-lead">Static website are the which are usually been used and are benefited through the Professionals and Small Companies.</p>
  <p>The companies with fewer budgets can promote their products and services through the static website and gain a lot.</p>
</article>

<section class="abs about">
  <h2 class="section-title">A Little About Our Company</h2>
  <div class="copy">
    <p>E-Commerce is a major progress in technology that has changed the way in which the customers now purchase information, products and the services. It's the new way of providing an opportunity to make your products and services available in the global market 24 hours a day through Internet</p>
    <p>Northvale eSolutions is specialized in handling advanced web projects and the ongoing projects that require permanent maintenance and support .We like challenges and do complete these challenge with expertise we like solving questions that arises in such projects as these helps us to grow also. When considering advanced web development project, finding the right answers to the hard questions is a challenge for any firm, it includes expertise and enables Northvale eSolutions to specialize in advanced projects and ongoing projects that require permanent support and maintenance.</p>
    <p>To manage the static website HTML knowledge is the required. The simple website are also said as the static web as its embeded on a page.Static website is a simple way to get your message out to the public. Static website are cheaper and also it needs less maintenance too. It's the simplest, cheapest and also the basic thing the search engine picks it up very easily. We at Northvale provide .</p>
  </div>
</section>
<a class="abs read-more" href="#" style="left:30px;top:1068px">CLICK HERE TO READ MORE</a>

<aside>
  <h3 class="abs side-title" style="left:617px;top:485px">News from Our Blog</h3>
  <div class="abs post-title" style="left:618px;top:517px">E-Commerce is a major progress in technology</div>
  <p class="abs post-text" style="left:618px;top:552px">Changed the way in which the customers now purchase information, products and the services. It's the new way of providing an opportunity to make your products and services available</p>
  <div class="abs post-date" style="left:619px;top:610px">Posted On Jan.31.2012</div>
  <div class="abs post-title" style="left:618px;top:637px">E-Commerce is a major progress in technology</div>
  <p class="abs post-text" style="left:618px;top:672px">Changed the way in which the customers now purchase information, products and the services. It's the new way of providing</p>
  <div class="abs post-date" style="left:619px;top:715px">Posted On Jan.31.2012</div>
  <a class="abs view-all" href="#">CLICK HERE TO VIEW ALL</a>
  <div class="abs dotted"></div>
  <h3 class="abs side-title" style="left:617px;top:794px">Testimonials</h3>
  <blockquote class="abs testimonial">E-Commerce is a major progress in technology that has changed the way in which the customers now purchase information, products and the services. It's the new way of providing an opportunity to make your products and services available in the global market 24 hours a day through Internet
    <cite>By Author Name ...</cite>
  </blockquote>
  <div class="abs connect">Connect With Us</div>
  <div class="abs social-icons">
    <span style="background:#3b5b9a"></span><span style="background:#2a6fd0"></span><span style="background:#f08a1c"></span><span style="background:#3aa3dc"></span>
  </div>
  <div class="abs social-links">Circlebook &nbsp;|&nbsp; Searchly &nbsp;|&nbsp; RSS &nbsp;|&nbsp; Chirper</div>
</aside>

<footer>
  <div class="abs footer-left">Copyright © 2012 Company Name &nbsp;|&nbsp; All right reserved<br>Terms &amp; Conditions &nbsp;|&nbsp; Privacy Policy</div>
  <nav class="abs footer-nav">Home &nbsp;|&nbsp; Services &nbsp;|&nbsp; About Us &nbsp;|&nbsp; SEO &nbsp;|&nbsp; SEM &nbsp;|&nbsp; Blog &nbsp;|&nbsp; Contact Us</nav>
</footer>
</body>
</html>
```